Business Card Design for Varomir Facility Services

We are looking for a Business Card Design for the Company "Varomir Facility Services."
Front side:
- Company Logo (small)
- Company Name, address, pohone, website and personal data.
- white background, for text e.g. company colors (blue or green like in the logo)
Please use following data:
Company data:
Varomir Facility Services Kostelac
Birkenhaldweg 14
6335 Rüstwil
www.varomir-fs.ch
Person data:
Tarik Kostelac
Geschäftsführer
+41 76 519 47 83
info@varomir-fs.ch
Back side:
could be colored in blue or green
please use a big logo sing and some smaller icons to say what is all beeing offered in facility services, like cleaning, maintenance cleaning
industrial cleaning, caretaking, gardening, disposal. There is no need for everyone of the icons if there are similar or an icon is standing for more of them.
colors to use:
blue: HEX 246BB0
green: HEX 52B33E

```html
<!DOCTYPE html>
<html lang="de">
<head>
<meta charset="utf-8">
<title>Varomir Facility Services – Visitenkarte</title>
<link rel="stylesheet" href="https://fonts.googleapis.com/css2?family=Montserrat:wght@500;600;700&display=swap">
<style>
  :root {
    --brand-blue: #246BB0;
    --brand-green: #52B33E;
    --card-white: #ffffff;
    --stage-grey: #d6d6d6;
    --icon-tint: rgba(255, 255, 255, 0.28);
  }
  * { margin: 0; padding: 0; box-sizing: border-box; }
  html, body {
    width: 1200px;
    height: 900px;
    overflow: hidden;
    background: var(--stage-grey);
    font-family: "Montserrat", Arial, sans-serif;
  }
  .card-sheet {
    width: 1200px;
    height: 900px;
    display: flex;
    align-items: center;
    justify-content: center;
    gap: 48px;
  }
  .business-card {
    width: 520px;
    height: 300px;
    display: block;
    box-shadow: 0 8px 22px rgba(0, 0, 0, 0.18);
  }
  .fill-blue { fill: var(--brand-blue); }
  .fill-green { fill: var(--brand-green); }
  .fill-white { fill: var(--card-white); }
  .stroke-blue { stroke: var(--brand-blue); fill: none; }
  .stroke-green { stroke: var(--brand-green); fill: none; }
  .icon-slot { fill: var(--icon-tint); }

  .brand-name-back { font-weight: 700; font-size: 27px; fill: var(--card-white); letter-spacing: 0.5px; }
  .brand-tagline-back { font-weight: 700; font-size: 14px; fill: var(--card-white); letter-spacing: 2px; }
  .service-label { font-weight: 500; font-size: 11.5px; fill: var(--card-white); }

  .brand-name-front { font-weight: 700; font-size: 19px; fill: var(--brand-blue); letter-spacing: 0.4px; }
  .brand-tagline-front { font-weight: 700; font-size: 10.5px; fill: var(--brand-blue); letter-spacing: 1.6px; }
  .person-name { font-weight: 700; font-size: 15px; fill: var(--brand-green); }
  .person-role { font-weight: 500; font-size: 11.5px; fill: var(--brand-blue); }
  .contact-line { font-weight: 500; font-size: 11.5px; fill: var(--brand-blue); }
  .contact-icon { fill: none; stroke: var(--brand-green); stroke-width: 1.4; stroke-linecap: round; stroke-linejoin: round; }
</style>
</head>
<body>
<main class="card-sheet">

  <!-- Back side: services -->
  <svg class="business-card card-back" viewBox="0 0 520 300" aria-label="Rückseite der Visitenkarte">
    <rect class="fill-blue" width="520" height="300"/>
    <path class="fill-green" d="M210,0 C330,30 390,160 400,300 L520,300 L520,0 Z"/>
    <path class="stroke-blue" stroke-width="3" d="M222,14 C330,48 378,160 388,300"/>

    <g class="brand-lockup">
      <circle class="fill-green" cx="52" cy="176" r="9"/>
      <text class="brand-name-back" x="70" y="170">Varomir</text>
      <text class="brand-tagline-back" x="70" y="200">FACILITY SERVICES</text>
    </g>

    <g class="service-list">
      <rect class="icon-slot" x="318" y="26" width="26" height="26" rx="4" role="img" aria-label="Icon Reinigung"/>
      <text class="service-label" x="354" y="43">Cleaning</text>

      <rect class="icon-slot" x="350" y="76" width="26" height="26" rx="4" role="img" aria-label="Icon Unterhaltsreinigung"/>
      <text class="service-label" x="386" y="86">Maintenance</text>
      <text class="service-label" x="386" y="100">Cleaning</text>

      <rect class="icon-slot" x="374" y="126" width="26" height="26" rx="4" role="img" aria-label="Icon Industriereinigung"/>
      <text class="service-label" x="410" y="136">Industrial</text>
      <text class="service-label" x="410" y="150">Cleaning</text>

      <rect class="icon-slot" x="392" y="178" width="26" height="26" rx="4" role="img" aria-label="Icon Gartenpflege"/>
      <text class="service-label" x="428" y="195">Gardening</text>

      <rect class="icon-slot" x="404" y="230" width="26" height="26" rx="4" role="img" aria-label="Icon Entsorgung"/>
      <text class="service-label" x="440" y="247">Disposal</text>
    </g>
  </svg>

  <!-- Front side: contact -->
  <svg class="business-card card-front" viewBox="0 0 520 300" aria-label="Vorderseite der Visitenkarte">
    <rect class="fill-white" width="520" height="300"/>
    <path class="fill-blue" d="M360,0 L520,0 L520,300 L478,300 C470,170 440,70 360,0 Z"/>
    <path class="stroke-green" stroke-width="6" d="M340,6 C420,60 455,170 462,300"/>

    <g class="brand-lockup">
      <circle class="fill-green" cx="46" cy="82" r="8"/>
      <text class="brand-name-front" x="62" y="80">Varomir</text>
      <text class="brand-tagline-front" x="62" y="98">FACILITY SERVICES</text>
    </g>

    <g class="person-block">
      <text class="person-name" x="40" y="152">Tarik Kostelac</text>
      <text class="person-role" x="40" y="168">Geschäftsführer</text>
    </g>

    <g class="address-block">
      <text class="contact-line" x="40" y="198">Birkenhaldweg 14</text>
      <text class="contact-line" x="40" y="213">6335 Rüstwil</text>
    </g>

    <g class="contact-block">
      <path class="contact-icon" d="M42,230 c0,5 4,9 9,9 l1.5,-2 -2.5,-2 -1.5,1 c-1.5,-1 -2.5,-2 -3.5,-3.5 l1,-1.5 -2,-2.5 z"/>
      <text class="contact-line" x="58" y="239">+41 76 519 47 83</text>

      <rect class="contact-icon" x="42" y="247" width="10" height="7" rx="1"/>
      <path class="contact-icon" d="M42,247 l5,4 5,-4"/>
      <text class="contact-line" x="58" y="255">info@varomir-fs.ch</text>

      <circle class="contact-icon" cx="47" cy="267" r="5"/>
      <path class="contact-icon" d="M42,267 h10 M47,262 c-2.5,3 -2.5,7 0,10 M47,262 c2.5,3 2.5,7 0,10"/>
      <text class="contact-line" x="58" y="271">www.varomir-fs.ch</text>
    </g>
  </svg>

</main>
</body>
</html>
```